Pet store web design

I would like to redesign my current online store (http://furrowlanemart.com)
I'm looking for a clean, modern design. Any ideas are welcome..

Industry/Entity Type

Pet

Number of Pages Required

3 page

```html
<!DOCTYPE html>
<html lang="en">
<head>
<meta charset="utf-8">
<title>Furrow Lane Mart — Pet Store</title>
<link rel="stylesheet" href="https://fonts.googleapis.com/css2?family=Open+Sans:wght@400;600;700;800&display=swap">
<style>
:root{
  --dark:#2e2320;
  --dark-2:#3a2d29;
  --yellow:#f7c21b;
  --yellow-deep:#f0b400;
  --coral:#ef5d4f;
  --orange:#f5a021;
  --blue:#1f9fe0;
  --red:#e8452f;
  --text:#4a4a4a;
  --muted:#9a9a9a;
  --light:#f4f4f4;
  --white:#ffffff;
}
*{box-sizing:border-box;margin:0;padding:0}
html,body{width:1200px;height:2168px;overflow:hidden}
body{font-family:"Open Sans",Arial,sans-serif;color:var(--text);background:var(--white);position:relative}
.wrap{width:1008px;margin:0 auto;position:relative}

.topbar{height:32px;background:#1f1714;color:#cfc6c2;font-size:11px}
.topbar .wrap{display:flex;justify-content:space-between;align-items:center;height:32px}
.topbar nav span{margin-right:22px}
.topbar .right span{margin-left:22px}

.header{height:112px;background:var(--dark)}
.header .wrap{display:flex;align-items:center;height:112px}
.brand{display:flex;align-items:center;gap:10px;background:var(--yellow);padding:12px 18px;border-radius:6px}
.brand .dot{width:22px;height:22px;border-radius:50%;background:var(--dark)}
.brand b{font-size:18px;font-weight:800;color:var(--dark)}
.contact-strip{margin-left:auto;display:flex;gap:40px;color:#e6deda;font-size:12px;margin-top:-30px}
.contact-strip div{display:flex;align-items:center;gap:10px}
.icon-box{width:28px;height:28px;border-radius:4px;background:var(--yellow);display:flex;align-items:center;justify-content:center}

.mainnav{position:absolute;right:96px;top:134px;width:520px;height:42px;background:var(--yellow);display:flex;justify-content:space-around;align-items:center;font-size:12px;font-weight:700;color:var(--dark);z-index:2}

.hero{height:580px;position:relative;background:linear-gradient(160deg,#6b3d1b 0%,#a8632a 35%,#d78a3a 60%,#8a4c1e 100%)}
.hero .frame{position:absolute;left:330px;top:150px;width:540px;height:230px;border:4px solid var(--white);border-radius:110px}
.hero .copy{position:absolute;left:0;right:0;top:196px;text-align:center;color:var(--white)}
.hero h1{font-size:54px;font-weight:800;letter-spacing:2px;line-height:1}
.hero h2{font-size:20px;font-weight:700;letter-spacing:3px;margin-top:8px}
.hero .from{font-size:13px;margin-top:14px;text-decoration:line-through;opacity:.8}
.hero .price{font-size:56px;font-weight:300;line-height:1}
.hero .price sup{font-size:28px}
.hero .arrow{position:absolute;top:270px;font-size:40px;color:var(--white);opacity:.8}

.promos{display:flex;gap:24px;margin-top:32px}
.promo{flex:1;height:196px;border-radius:4px;position:relative;overflow:hidden;color:var(--white);padding:22px}
.promo h3{font-size:22px;font-weight:800;line-height:1.1}
.promo p{font-size:12px;margin-top:4px}
.promo .btn{display:inline-block;margin-top:14px;background:var(--white);color:var(--dark);font-size:10px;font-weight:700;padding:6px 12px;border-radius:2px}
.promo .art{position:absolute;right:14px;bottom:0;width:130px;height:150px;border-radius:8px 8px 0 0;opacity:.55}
.p1{background:var(--red)} .p1 .art{background:linear-gradient(#fbd46a,#c9862f)}
.p2{background:var(--orange)} .p2 .art{background:linear-gradient(#dcdcdc,#8e8e8e)}
.p3{background:var(--blue)} .p3 .art{background:linear-gradient(#f3e05a,#4bb05e)}

.section-title{display:flex;justify-content:space-between;align-items:center;margin-top:48px}
.section-title h4{font-size:20px;font-weight:800;color:var(--dark)}
.pager{display:flex;gap:6px}
.pager span{width:18px;height:18px;border-radius:50%;background:#ccc}
.rule{height:2px;background:#eee;margin-top:10px}

.products{display:flex;gap:24px;margin-top:24px}
.card{flex:1;height:372px;border:1px solid #e5e5e5;text-align:center;padding:16px}
.card .photo{height:200px;border-radius:4px}
.card p{font-size:11px;color:var(--muted);margin-top:14px;line-height:1.5}
.card .cost{color:var(--coral);font-weight:700;font-size:14px;margin-top:10px}
.card .add{display:inline-block;background:var(--yellow);font-size:10px;font-weight:700;padding:7px 18px;margin-top:10px;color:var(--dark)}

.newbar{margin-top:48px;height:160px;background:var(--yellow);display:flex;align-items:center;position:relative}
.newbar .txt{padding-left:80px;color:var(--white)}
.newbar .txt b{font-size:44px;font-weight:800;display:block;line-height:1}
.newbar .txt span{font-size:15px;font-weight:700;letter-spacing:1px}
.newbar .photo{position:absolute;right:0;top:0;width:400px;height:160px;background:linear-gradient(90deg,var(--yellow),#c9b99c 30%,#8a7a62)}

.features{display:flex;justify-content:space-between;margin-top:34px;font-size:11px}
.feature{display:flex;gap:12px;align-items:center}
.feature b{display:block;color:var(--dark);font-size:11px}
.feature small{color:var(--muted)}

.newsletter{margin-top:32px;height:96px;display:flex}
.newsletter .social{width:428px;background:var(--dark-2);display:flex;align-items:center;justify-content:center;gap:14px}
.newsletter .social span{width:26px;height:26px;border-radius:50%;background:#5a4a45}
.newsletter .signup{flex:1;background:var(--coral);display:flex;align-items:center;padding:0 32px;color:var(--white);gap:20px}
.signup h5{font-size:20px;font-weight:700}
.signup p{font-size:11px}
.signup .field{margin-left:auto;width:200px;height:34px;background:var(--white);color:var(--muted);font-size:11px;padding:10px}
.signup .go{height:34px;background:var(--yellow);color:var(--dark);font-size:11px;font-weight:700;padding:10px 16px;margin-left:-20px}

.footer{background:var(--dark);height:304px;color:#bdb3ae;font-size:11px}
.footer .wrap{display:flex;padding-top:36px;gap:40px}
.footer .col{flex:1}
.footer .col:first-child{flex:1.4}
.footer h6{color:var(--white);font-size:15px;font-weight:700;margin-bottom:14px}
.footer li{list-style:none;line-height:2}
.footer .about{margin-top:16px;line-height:1.7}
.legal{background:#1f1714;height:40px;color:#8e837f;font-size:10px}
.legal .wrap{display:flex;justify-content:space-between;align-items:center;height:40px}
.cards{display:flex;gap:6px}
.cards span{width:34px;height:20px;background:#fff;border-radius:2px}
</style>
</head>
<body>

<div class="topbar"><div class="wrap">
  <nav><span>LOGIN</span><span>ABOUT US</span><span>CONTACT US</span><span>PRODUCT</span></nav>
  <div class="right"><span>Create an Account</span><span>MY ACCOUNT</span><span>LANGUAGE</span></div>
</div></div>

<header class="header"><div class="wrap">
  <div class="brand"><span class="dot"></span><b>Furrow Lane Mart</b></div>
  <div class="contact-strip">
    <div><span class="icon-box"><svg width="14" height="14" viewBox="0 0 14 14"><rect x="1" y="3" width="12" height="8" fill="none" stroke="#2e2320" stroke-width="1.6"/></svg></span>IN STOCK QUEUE</div>
    <div><span class="icon-box"><svg width="14" height="14" viewBox="0 0 14 14"><path d="M3 1l3 3-2 2c1 2 2 3 4 4l2-2 3 3-2 2C6 13 1 8 1 3z" fill="#2e2320"/></svg></span>CALL US +1 (555) 014 2760</div>
  </div>
</div></header>

<nav class="mainnav"><span>HOME</span><span>DOG</span><span>CAT</span><span>FISH</span><span>BIRD</span><span>SMALL PET</span></nav>

<section class="hero" role="img" aria-label="Photo of a puppy and a shepherd dog lying in autumn leaves">
  <div class="frame"></div>
  <div class="copy">
    <h1>EVERY</h1>
    <h2>FURROW LANE STORE</h2>
    <div class="from">from $12.99</div>
    <div class="price">$8<sup>99</sup></div>
  </div>
  <span class="arrow" style="left:30px">&#8249;</span>
  <span class="arrow" style="right:30px">&#8250;</span>
</section>

<main class="wrap">
  <div class="promos">
    <div class="promo p1"><h3>FALL &amp; WINTER</h3><p>Warm coats for pups</p><span class="btn">SHOP NOW</span><div class="art" role="img" aria-label="Dog in sunglasses"></div></div>
    <div class="promo p2"><h3>KEEP YOUR PET</h3><p>Warm and safe</p><span class="btn">SHOP NOW</span><div class="art" role="img" aria-label="Grey cat"></div></div>
    <div class="promo p3"><h3>TOO FAST FOR</h3><p>Fun chew toys</p><span class="btn">SHOP NOW</span><div class="art" role="img" aria-label="Colourful pet toy"></div></div>
  </div>

  <div class="section-title"><h4>MOST POPULAR</h4><div class="pager"><span></span><span></span></div></div>
  <div class="rule"></div>

  <div class="products">
    <div class="card"><div class="photo" role="img" aria-label="Small dog in a knit sweater" style="background:linear-gradient(#eef2f7,#b9c6d8)"></div><p>Cozy knit sweater for small dogs, soft and warm</p><div class="cost">£10.99</div><span class="add">ADD TO CART</span></div>
    <div class="card"><div class="photo" role="img" aria-label="Dog in a green vest" style="background:linear-gradient(#f3f6ee,#9fcf6a)"></div><p>Bright padded vest for walks in cold weather</p><div class="cost">£10.99</div><span class="add">ADD TO CART</span></div>
    <div class="card"><div class="photo" role="img" aria-label="Round green pet bed" style="background:linear-gradient(#f4f6ec,#a7b96a)"></div><p>Round plush pet bed with raised soft edges</p><div class="cost">£10.99</div><span class="add">ADD TO CART</span></div>
    <div class="card"><div class="photo" role="img" aria-label="Dog on a training mat" style="background:linear-gradient(#f2f2f2,#7a8a6a)"></div><p>Indoor grass training mat, easy to clean</p><div class="cost">£10.99</div><span class="add">ADD TO CART</span></div>
  </div>

  <div class="newbar">
    <div class="txt"><b>30 NEW</b><span>PET PRODUCTS EVERY MONTH</span></div>
    <div class="photo" role="img" aria-label="Terrier dog lying on the floor"></div>
  </div>

  <div class="features">
    <div class="feature"><svg width="26" height="18" viewBox="0 0 26 18"><rect x="1" y="2" width="15" height="11" fill="none" stroke="#777" stroke-width="1.5"/><path d="M16 6h5l4 4v3h-9" fill="none" stroke="#777" stroke-width="1.5"/><circle cx="6" cy="15" r="2" fill="#777"/><circle cx="20" cy="15" r="2" fill="#777"/></svg><div><b>FREE SHIPPING ITEM</b><small>On all orders over £50</small></div></div>
    <div class="feature"><svg width="20" height="20" viewBox="0 0 20 20"><path d="M16 10a6 6 0 1 1-2-4.5M16 2v4h-4" fill="none" stroke="#777" stroke-width="1.5"/></svg><div><b>30 DAYS FREE RETURN</b><small>Easy returns, no fuss</small></div></div>
    <div class="feature"><svg width="22" height="18" viewBox="0 0 22 18"><rect x="1" y="2" width="20" height="14" rx="2" fill="none" stroke="#777" stroke-width="1.5"/><path d="M1 7h20" stroke="#777" stroke-width="1.5"/></svg><div><b>CASH ON DELIVERY</b><small>Pay when your order arrives</small></div></div>
  </div>
</main>

<section class="wrap newsletter">
  <div class="social"><span></span><span></span><span></span><span></span><span></span></div>
  <div class="signup">
    <svg width="30" height="22" viewBox="0 0 30 22"><rect x="1" y="1" width="28" height="20" fill="none" stroke="#fff" stroke-width="2"/><path d="M1 1l14 11L29 1" fill="none" stroke="#fff" stroke-width="2"/></svg>
    <div><h5>Join our Newsletter</h5><p>Sign up to stay up to date with our latest news</p></div>
    <div class="field">Email</div><div class="go">SUBSCRIBE</div>
  </div>
</section>

<footer class="footer"><div class="wrap">
  <div class="col">
    <div class="brand" style="display:inline-flex"><span class="dot"></span><b>Furrow Lane Mart</b></div>
    <p class="about">Everything your pets need in one friendly shop. Quality food, toys, beds and care products picked by pet lovers, delivered to your door at fair prices every day.</p>
  </div>
  <div class="col"><h6>SERVICES</h6><ul><li>Pet Grooming</li><li>Pet Adoption</li><li>Gift Bag Maker</li><li>Pet Hotel</li><li>Puppy School</li></ul></div>
  <div class="col"><h6>MY ACCOUNT</h6><ul><li>Delivery Information</li><li>Privacy Policy</li><li>Returns Policy</li><li>Terms and Conditions</li><li>FAQs</li></ul></div>
  <div class="col"><h6>CONTACTS</h6><ul><li>14 Orchard Row, Millbrook</li><li>Help: +1 (555) 014 2760</li><li>support@furrowlanemart.com</li></ul></div>
</div></footer>

<div class="legal"><div class="wrap">
  <span>All Rights Reserved. Copyright © 2015 Furrow Lane Mart</span>
  <div class="cards"><span></span><span></span><span></span><span></span></div>
</div></div>

</body>
</html>
```